Snoutsaver.net Dog Coupon Site Website Design

TailThrift - Dog Coupon Site Design Brief

Project Overview
**Site Name:** SnoutSaver.net
**Purpose:** A modern coupon aggregation platform specifically for dog and pet-related products and services
**Target Audience:** Dog owners, pet enthusiasts, budget-conscious pet parents

Brand Identity & Visual Direction

Typography
- **Headers:** Modern sans-serif (Inter or similar) - Clean and friendly
- **Body:** Readable sans-serif with good mobile legibility
- **Accent:** Playful but professional font for coupon codes

Design Principles
- **Flat Design:** Clean, minimal with subtle shadows
- **Friendly & Approachable:** Rounded corners, soft edges
- **Trust-Building:** Clear pricing, transparent savings
- **Scannable:** Easy-to-read coupon codes and offers

## User Experience & Functionality

### Homepage Features
1. **Hero Section**
- Clear value proposition
- Search functionality
- Featured savings highlight

2. **Coupon Cards**
- One-click copy functionality
- Clear discount display
- Store/brand logos
- Expiration dates
- "Get Deal" call-to-action

3. **Navigation**
- Categories (Food, Toys, Health, Services, etc.)
- Popular stores
- Latest deals

### Interactive Elements
- **Copy Button:** Instant feedback when coupon copied
- **Deal Pages:** Detailed offer information, terms, store details
- **Search & Filter:** By category, store, discount amount
- **Mobile Menu:** Hamburger navigation for mobile

## Technical Requirements

### Responsive Design
- **Mobile-First:** Optimized for touch interactions
- **Tablet:** Adapted layout for medium screens
- **Desktop:** Full-width utilization with sidebar potential

### Performance
- **Fast Loading:** Optimized images, minimal JavaScript
- **Accessibility:** WCAG compliant, screen reader friendly
- **SEO Optimized:** Structured data for deals and offers

## Content Strategy

### Deal Categories
- Dog Food & Treats
- Toys & Accessories
- Health & Grooming
- Training & Services
- Outdoor & Travel

### Key Messaging
- "Save on everything your dog loves"
- "Verified deals updated daily"
- "Your pup deserves the best for less"

## Conversion Optimization

### Trust Elements
- Deal verification badges
- User reviews/ratings
- Clear savings calculations
- Expiration date transparency

### Call-to-Actions
- "Copy Code" (primary action)
- "Get Deal" (secondary action)
- "View All [Store] Deals"

## Success Metrics
- Coupon copy rate
- Click-through to retailer
- User return visits
- Mobile vs desktop usage
- Category performance

This design brief ensures a user-friendly, trustworthy platform that makes finding and using pet deals effortless while maintaining a warm, dog-loving community feel.

1. Design Objective
Create a warm, energetic space where dog lovers instantly feel welcomed and confident they’re finding genuine savings for their furry friends. Everything from the layout to the smallest icon should reinforce trust, delight, and simplicity.
2. Visual Personality
Color Palette: Soft, cheerful hues—think warm yellows and gentle blues—that evoke sunshine and playfulness without overwhelming.
Typography:
Headings: A modern, friendly sans‑serif (like Inter) with open letterforms to feel approachable.
Body Copy: Highly legible sans‑serif with generous line spacing for comfort on small screens.
Accent Font: A slightly quirky, hand‑drawn style used sparingly for coupon codes and special call‑outs, giving a personal, “paw‑picked” touch.
Imagery & Icons: Real‑life photographs of happy dogs interspersed with clean line‑icons of bones, paw prints, and hearts. Rounded shapes and subtle shadows keep the look soft and contemporary.
3. Layout & Hierarchy
Hero Area:
Full‑bleed image of a joyful dog, overlaid with a single, punchy tagline (“Save on everything your dog loves”).
Prominent search bar centered to invite exploration.
Offer Grid:
Generous white space around each coupon card so the eye can rest and scan easily.
Coupon cards feature a bold discount label, brand logo, and a friendly “Get Deal” button.
A playful “Copied!” animation briefly replaces the button once the code is grabbed.
Navigation:
A fixed header with clear category labels (Food, Toys, Health, Services).
A secondary “Popular Stores” carousel below to spotlight key partners.
4. Interaction & Motion
Micro‑interactions:
Hover state for cards subtly lifts the card and deepens its shadow, inviting a click.
Copy‑code button pulses once on hover, hinting at its one‑click magic.
Transitions:
Smooth fades between deal filters and search results to reassure users that the site is responding.
Loading indicators shaped like spinning collars or wagging tails to keep the theme consistent.
5. Accessibility & Inclusivity
Ensure all text meets contrast standards so every pet parent—regardless of vision—can read offers with ease.
Interactive elements sized for easy tapping on touchscreens.
Alt‑text for all imagery describing dogs, products, and actions for screen‑reader users.
6. Emotional Tone
From the moment someone lands on SnoutSaver.net, they should feel the joy of treating their dog without guilt. Friendly copy (“Your pup deserves the best for less”) paired with bright visuals will create a sense of community and shared passion.
7. Success by Design
Scan‑ability: Users should spot great deals in under two seconds.
Trust Signals: Badges (“Verified Savings”), clear expiration dates, and reviewer star icons should feel earned and prominent.
Return Visits: A “My Favorite Deals” heart icon encourages saving and returning, reinforced by subtle reminders in the UI.
This design approach keeps dog lovers front and center—making sure every graphic, font choice, and interaction feels like it was lovingly tailored for them.

Target Market(s)

Dog Lovers looking for good deals

Industry/Entity Type

Coupon Code

Number of Pages Required

4 page

Font styles to use
Sans Serif

Requirements
Must have
• Modern look, coupon copy cards it's a deal site and I want the coupon code and copy in the coupon card, blog section, review section, modern footer/header
Nice to have
• Modern coupon code website, easy to use

```html
<!DOCTYPE html>
<html lang="en">
<head>
<meta charset="utf-8">
<title>SnoutSaver – Save On Everything Your Dog Loves</title>
<link rel="stylesheet" href="https://fonts.googleapis.com/css2?family=Inter:wght@300;400;500;600;700;800&family=Montserrat:wght@400;500;600&display=swap">
<style>
:root{
  --cream:#fffaea;
  --ink:#111111;
  --muted:#444444;
  --yellow:#fbe38a;
  --yellow-deep:#f6d96b;
  --peach:#f7c9bd;
  --peach-bg:#fbece8;
  --sky:#bfe7f7;
  --sky-bg:#eef7fb;
  --orange:#f3a53c;
  --blob-pink:#f4c3b6;
  --blob-orange:#f5b658;
  --dog-brown:#a8582f;
  --white:#ffffff;
  --black:#000000;
}
*{box-sizing:border-box;margin:0;padding:0}
html,body{width:1200px;height:4191px;overflow:hidden}
body{font-family:"Inter",sans-serif;color:var(--ink);background:var(--white);position:relative}
section,header,footer{position:absolute;left:0;width:1200px}
.abs{position:absolute}
.section-title{position:absolute;left:0;width:1200px;text-align:center;font-size:31px;font-weight:400}
.section-title b{font-weight:700}
.title-bar{position:absolute;left:496px;width:211px;height:7px;border-radius:6px;background:var(--yellow)}
.arrow{position:absolute;width:30px;height:30px;border:1.5px solid #222;border-radius:50%;display:flex;align-items:center;justify-content:center}
.btn{display:flex;align-items:center;justify-content:center;font-weight:700;font-size:16px;color:var(--ink)}
.stars{color:var(--orange);font-size:13px;letter-spacing:1px}

/* hero */
.hero{top:0;height:626px;background:var(--cream);overflow:hidden}
.brand{left:111px;top:26px;font-size:28px;font-weight:700}
.nav{right:108px;top:28px;display:flex;align-items:center;font-size:15px}
.nav a{color:var(--ink);text-decoration:none;padding:6px 16px}
.nav a.active{background:var(--yellow-deep);border-radius:6px;font-weight:700}
.hero-title{left:107px;top:126px;font-size:62px;line-height:68px;font-weight:400}
.hero-title strong{font-weight:800}
.hero-bar{left:325px;top:340px;width:205px;height:8px;border-radius:8px;background:var(--yellow-deep);transform:rotate(-1deg)}
.hero-copy{left:111px;top:367px;width:430px;font-size:14px;line-height:27px;color:var(--muted)}
.search{left:111px;top:437px;width:417px;height:49px;background:var(--white);border:1.5px solid #e2e2e2;border-radius:4px;display:flex;align-items:center;justify-content:space-between;padding:0 8px 0 26px;font-size:14px;color:#333}
.search-btn{width:38px;height:32px;border-radius:4px;background:var(--yellow-deep);display:flex;align-items:center;justify-content:center}
.hero-shapes{left:580px;top:100px}
.hero-dog{left:720px;top:130px;width:320px;height:496px;border-radius:150px 150px 0 0;background:linear-gradient(180deg,#b8663a 0%,#a3542c 45%,#8e4724 80%,#c9a58a 100%)}

/* coupons */
.coupons{top:626px;height:683px;background:var(--white)}
.coupon{position:absolute;top:195px;width:272px;height:390px;background:var(--white);border:1px solid #ececec;border-radius:14px;box-shadow:0 8px 16px rgba(0,0,0,.08)}
.coupon.active{background:#e6f5fb}
.coupon-store{position:absolute;left:22px;top:26px;font-size:17px;font-weight:700;display:flex;align-items:center;gap:7px}
.coupon-store i{display:block;width:14px;height:14px;background:#222;border-radius:3px}
.expiry{position:absolute;right:16px;top:22px;background:#f1f1f1;border-radius:14px;padding:6px 12px;font-size:14px}
.tag{position:absolute;left:90px;top:82px;width:104px;height:60px;background:var(--yellow);border-radius:6px;transform:rotate(-28deg);display:flex;align-items:center;justify-content:center;font-weight:800;font-size:18px}
.icon-slot{position:absolute;left:108px;top:170px;width:58px;height:58px;border-radius:12px;background:#fbe9e2}
.coupon.active .icon-slot{background:#f7dcd0}
.coupon p{position:absolute;left:0;top:252px;width:100%;text-align:center;font-size:15px;line-height:26px;color:#333}
.coupon .btn{position:absolute;left:78px;top:314px;width:115px;height:36px;border-radius:3px;background:var(--peach)}
.coupon.active .btn{background:var(--sky)}

/* categories */
.categories{top:1309px;height:759px;background:var(--peach-bg)}
.cat{position:absolute;background:var(--white);border-radius:14px;box-shadow:0 4px 10px rgba(0,0,0,.05)}
.cat .photo{position:absolute;border-radius:16px}
.cat-label{position:absolute;left:0;width:100%;text-align:center;font-size:22px;font-weight:500}
.toys-title{position:absolute;left:395px;top:34px;font-size:22px;font-weight:500}
.toys-copy{position:absolute;left:395px;top:72px;width:265px;font-size:13.5px;line-height:22px;color:#333}
.toys-btn{position:absolute;left:395px;top:153px;width:110px;height:36px;background:var(--peach);border-radius:3px;font-size:15px}

/* reviews */
.reviews{top:2068px;height:509px;background:var(--white)}
.review{position:absolute;top:176px;width:434px;height:232px;border:1.5px solid #e9e9e9;border-radius:8px;font-family:"Montserrat",sans-serif;box-shadow:0 3px 8px rgba(0,0,0,.04)}
.avatar{position:absolute;left:32px;top:20px;width:73px;height:73px;border-radius:50%;background:linear-gradient(180deg,#d8d2ca 0%,#8f7f72 60%,#3f3631 100%)}
.review-name{position:absolute;left:136px;top:22px;font-size:16px;font-weight:600}
.review-treat{position:absolute;left:136px;top:50px;font-size:14px}
.review .stars{position:absolute;left:136px;top:73px;font-size:14px}
.review-body{position:absolute;left:32px;top:112px;width:375px;font-size:13px;line-height:24px;color:#444}
.chev{position:absolute;top:2335px}

/* deals */
.deals{top:2577px;height:708px;background:var(--sky-bg)}
.deal{position:absolute;top:171px;width:226px;height:345px;background:var(--white);border-radius:14px;border:1px solid #ececec;box-shadow:0 6px 12px rgba(0,0,0,.06)}
.deal-badge{position:absolute;right:12px;top:12px;border:1px solid #cfcfcf;border-radius:12px;padding:3px 14px;font-size:13px;background:#fffdf4}
.deal .photo{position:absolute;left:28px;top:48px;width:170px;height:124px;border-radius:12px}
.deal-price{position:absolute;left:36px;top:188px;font-size:15px}
.deal-name{position:absolute;left:36px;top:215px;font-size:15px;font-weight:500}
.deal .stars{position:absolute;left:36px;top:242px}
.deal .btn{position:absolute;left:34px;top:280px;width:158px;height:35px;background:var(--peach);border-radius:3px;font-size:15px}
.view-all{position:absolute;height:44px;background:var(--sky);border-radius:2px;font-size:17px}

/* stores */
.stores{top:3285px;height:475px;background:var(--white)}
.store{position:absolute;top:196px;width:180px;display:flex;flex-direction:column;align-items:center;gap:10px;font-size:19px;font-weight:600;letter-spacing:.5px;color:#333}
.store i{display:block;width:64px;height:64px;border-radius:50%;background:#4a4a4a}

/* footer */
.footer{top:3760px;height:431px;background:var(--black);color:var(--white)}
.foot-head{position:absolute;top:63px;font-size:21px;font-weight:600}
.foot-links{position:absolute;top:98px;list-style:none;font-size:14.5px;line-height:31px}
.contact{position:absolute;left:507px;display:flex;align-items:center;gap:16px;font-size:14.5px}
.contact i{width:36px;height:36px;border-radius:50%;background:var(--peach);display:flex;align-items:center;justify-content:center}
.news-copy{position:absolute;left:828px;top:116px;width:300px;font-size:14px;line-height:31px}
.news-input{position:absolute;left:831px;top:182px;width:270px;border-bottom:1.5px solid var(--white);padding-bottom:8px;font-size:14px}
.subscribe{position:absolute;left:836px;top:243px;width:133px;height:52px;background:var(--peach);border-radius:2px;font-size:17px}
.foot-rule{position:absolute;left:97px;top:367px;width:1049px;height:1px;background:#888}
.copyright{position:absolute;left:0;top:388px;width:1200px;text-align:center;font-size:14px}
</style>
</head>
<body>

<header class="hero">
  <div class="abs brand">SnoutSaver</div>
  <nav class="abs nav">
    <a class="active">Home</a><a>Categories</a><a>Popular stores</a><a>Latest deals</a>
  </nav>
  <h1 class="abs hero-title">Save On<br>Everything Your<br><strong>Dog Loves</strong></h1>
  <div class="abs hero-bar"></div>
  <p class="abs hero-copy">Lorem ipsum dolor sit amet, consectetur adipiscing elit, sed do eiusmod tempor incididunt ut labore et dolore magna aliqua.</p>
  <div class="abs search">By category, store, discount amount
    <span class="search-btn"><svg width="16" height="16" viewBox="0 0 16 16" fill="none" stroke="#222" stroke-width="1.6"><circle cx="7" cy="7" r="5"/><path d="M11 11l3.5 3.5"/></svg></span>
  </div>
  <svg class="abs hero-shapes" width="620" height="526" viewBox="0 0 620 526" aria-hidden="true">
    <path d="M470 300 C560 300 580 420 520 450 C470 470 420 440 410 400 Z" fill="var(--blob-orange)"/>
    <path d="M60 526 C20 420 40 260 80 170 C120 60 230 40 280 90 C330 20 470 30 500 120 C530 200 520 300 470 360 C440 420 400 480 380 526 Z" fill="var(--blob-pink)"/>
  </svg>
  <div class="abs hero-dog" role="img" aria-label="Happy brown dog standing with a bone in its mouth"></div>
</header>

<section class="coupons">
  <h2 class="section-title" style="top:92px">Feature <b>Coupon Cards</b></h2>
  <div class="title-bar" style="top:151px"></div>
  <div class="arrow" style="left:45px;top:354px"><svg width="10" height="10" viewBox="0 0 10 10" fill="none" stroke="#222" stroke-width="1.5"><path d="M6.5 1.5L3 5l3.5 3.5"/></svg></div>
  <div class="arrow" style="left:1125px;top:354px"><svg width="10" height="10" viewBox="0 0 10 10" fill="none" stroke="#222" stroke-width="1.5"><path d="M3.5 1.5L7 5 3.5 8.5"/></svg></div>

  <article class="coupon" style="left:143px">
    <div class="coupon-store"><i></i>Pupnest</div>
    <div class="expiry">Expiry May 31</div>
    <div class="tag">30%Off</div>
    <div class="icon-slot" role="img" aria-label="Small line drawing of a sitting puppy"></div>
    <p>Lorem ipsum dolor sit amet,<br>consectetur adipiscing</p>
    <div class="btn">Get Deal</div>
  </article>
  <article class="coupon active" style="left:463px">
    <div class="coupon-store">Fetchly</div>
    <div class="expiry">Expiry May 31</div>
    <div class="tag">40%Off</div>
    <div class="icon-slot" role="img" aria-label="Small line drawing of a bone"></div>
    <p>Lorem ipsum dolor sit amet,<br>consectetur adipiscing</p>
    <div class="btn">Copied</div>
  </article>
  <article class="coupon" style="left:784px">
    <div class="coupon-store">Woofmart</div>
    <div class="expiry">Expiry May 31</div>
    <div class="tag">20%Off</div>
    <div class="icon-slot" role="img" aria-label="Small line drawing of a fish toy"></div>
    <p>Lorem ipsum dolor sit amet,<br>consectetur adipiscing</p>
    <div class="btn">Get Deal</div>
  </article>
</section>

<section class="categories">
  <h2 class="section-title" style="top:84px">Our <b>Categories</b></h2>
  <div class="title-bar" style="top:141px"></div>
  <div class="cat" style="left:111px;top:172px;width:273px;height:464px">
    <div class="photo" role="img" aria-label="Beagle sitting beside a bowl of dry dog food" style="left:22px;top:23px;width:231px;height:371px;background:linear-gradient(180deg,#7d6048 0%,#a58466 40%,#c9b7a3 65%,#b4772f 85%,#9a9a9a 100%)"></div>
    <div class="cat-label" style="top:412px">Food</div>
  </div>
  <div class="cat" style="left:411px;top:172px;width:675px;height:220px">
    <div class="photo" role="img" aria-label="Terrier with a rope toy beside a red toy wagon on grass" style="left:17px;top:13px;width:349px;height:194px;background:linear-gradient(180deg,#6e9a4e 0%,#a7c98a 45%,#d9574a 62%,#7fb04c 80%,#6a9a38 100%)"></div>
    <div class="toys-title">Toys</div>
    <p class="toys-copy">Lorem ipsum dolor sit amet, consectetur adipiscing elit, sed do eiusmod tempor incididunt ut labore et dolore aliqua.</p>
    <div class="btn toys-btn">Read More</div>
  </div>
  <div class="cat" style="left:411px;top:418px;width:319px;height:219px">
    <div class="photo" role="img" aria-label="Dog on a lead walking beside its owner on a yellow bridge" style="left:12px;top:11px;width:294px;height:150px;background:linear-gradient(90deg,#e3c23c 0%,#8c8a80 25%,#b3a996 55%,#7f7a70 80%,#e0bf3a 100%)"></div>
    <div class="cat-label" style="top:176px">Services</div>
  </div>
  <div class="cat" style="left:754px;top:418px;width:319px;height:219px">
    <div class="photo" role="img" aria-label="Veterinarian examining a golden dog with a stethoscope" style="left:12px;top:11px;width:294px;height:150px;background:linear-gradient(90deg,#eef0ee 0%,#e3e6e2 35%,#d9b77e 55%,#f3f4f6 75%,#7fa06a 100%)"></div>
    <div class="cat-label" style="top:176px">Health</div>
  </div>
</section>

<section class="reviews">
  <h2 class="section-title" style="top:81px">Client <b>Reviews</b></h2>
  <div class="title-bar" style="top:135px"></div>
  <article class="review" style="left:146px">
    <div class="avatar" role="img" aria-label="Portrait photo of the reviewer"></div>
    <div class="review-name">Miss S</div>
    <div class="review-treat">Treatment: ClearSmile</div>
    <div class="stars">★★★★★</div>
    <p class="review-body">Mr O wanted to close the gaps, so we did this with "no preparation" veneers, this is what he says "I cant believe how much my life has changed and how different I look. I would definitely recommend.</p>
  </article>
  <article class="review" style="left:620px">
    <div class="avatar" role="img" aria-label="Portrait photo of the reviewer"></div>
    <div class="review-name">Mr O</div>
    <div class="review-treat">Treatment: BrightVeneer</div>
    <div class="stars">★★★★★</div>
    <p class="review-body">Veneers &amp; Gum Lift After her treatment for mis-shaped teeth that she felt embarrassed about, this is what Miss S said "I feel so much more confident than 2 weeks ago</p>
  </article>
</section>
<svg class="chev" style="left:44px" width="22" height="44" viewBox="0 0 22 44" fill="none" stroke="#111" stroke-width="2"><path d="M20 2L2 22l18 20"/></svg>
<svg class="chev" style="left:1134px" width="22" height="44" viewBox="0 0 22 44" fill="none" stroke="#111" stroke-width="2"><path d="M2 2l18 20L2 42"/></svg>

<section class="deals">
  <h2 class="section-title" style="top:72px">Latest <b>Deals</b></h2>
  <div class="title-bar" style="top:124px"></div>
  <div class="arrow" style="left:44px;top:322px"><svg width="10" height="10" viewBox="0 0 10 10" fill="none" stroke="#222" stroke-width="1.5"><path d="M6.5 1.5L3 5l3.5 3.5"/></svg></div>
  <div class="arrow" style="left:1127px;top:322px"><svg width="10" height="10" viewBox="0 0 10 10" fill="none" stroke="#222" stroke-width="1.5"><path d="M3.5 1.5L7 5 3.5 8.5"/></svg></div>

  <article class="deal" style="left:111px">
    <div class="deal-badge">Deals</div>
    <div class="photo" role="img" aria-label="Metal bowl full of dry dog food" style="background:linear-gradient(180deg,#f7f3ee 0%,#b26c2c 30%,#c98a4a 55%,#c9c9c9 75%,#f7f3ee 100%)"></div>
    <div class="deal-price">$ 50.00</div><div class="deal-name">Language Growth</div>
    <div class="stars">★★★★☆</div><div class="btn">Shop Now</div>
  </article>
  <article class="deal" style="left:361px">
    <div class="deal-badge">Sales</div>
    <div class="photo" role="img" aria-label="Hot dog in a bun with mustard" style="background:linear-gradient(135deg,#fff 0%,#f1b35e 30%,#d8402a 50%,#f0a850 70%,#fff 100%)"></div>
    <div class="deal-price">$ 50.00</div><div class="deal-name">Language Growth</div>
    <div class="stars">★★★★☆</div><div class="btn">Shop Now</div>
  </article>
  <article class="deal" style="left:611px">
    <div class="deal-badge">Deals</div>
    <div class="photo" role="img" aria-label="Black puppy lying among carrots" style="background:linear-gradient(180deg,#fff 0%,#f29a5a 20%,#2a2a2a 45%,#3a3432 75%,#f4efe8 100%)"></div>
    <div class="deal-price">$ 50.00</div><div class="deal-name">Language Growth</div>
    <div class="stars">★★★★☆</div><div class="btn">Shop Now</div>
  </article>
  <article class="deal" style="left:862px">
    <div class="deal-badge">Sales</div>
    <div class="photo" role="img" aria-label="Brown leather dog collar with a metal tag" style="background:linear-gradient(180deg,#fff 0%,#fff 25%,#a85a2a 35%,#b8682f 55%,#fff 62%,#dcdcdc 80%,#fff 100%)"></div>
    <div class="deal-price">$ 50.00</div><div class="deal-name">Language Growth</div>
    <div class="stars">★★★★☆</div><div class="btn">Shop Now</div>
  </article>

  <div class="btn view-all" style="left:525px;top:560px;width:150px">View All Deals</div>
</section>

<section class="stores">
  <h2 class="section-title" style="top:89px">Popular <b>Stores</b></h2>
  <div class="title-bar" style="top:141px"></div>
  <div class="arrow" style="left:43px;top:227px"><svg width="10" height="10" viewBox="0 0 10 10" fill="none" stroke="#222" stroke-width="1.5"><path d="M6.5 1.5L3 5l3.5 3.5"/></svg></div>
  <div class="arrow" style="left:1117px;top:227px"><svg width="10" height="10" viewBox="0 0 10 10" fill="none" stroke="#222" stroke-width="1.5"><path d="M3.5 1.5L7 5 3.5 8.5"/></svg></div>
  <div class="store" style="left:107px"><i></i>Barkwell</div>
  <div class="store" style="left:310px"><i></i>Pawlane</div>
  <div class="store" style="left:515px"><i></i>Tailway</div>
  <div class="store" style="left:692px"><i></i>Furrow Co</div>
  <div class="store" style="left:897px"><i></i>Kibblery</div>
  <div class="btn view-all" style="left:525px;top:333px;width:156px;height:46px">View All Stores</div>
</section>

<footer class="footer">
  <div class="foot-head" style="left:97px">Quick Links</div>
  <ul class="foot-links" style="left:99px">
    <li>➔ Home</li><li>➔ About Us</li><li>➔ Menu</li><li>➔ Order Online</li><li>➔ What's New</li><li>➔ Contact Us</li>
  </ul>
  <div class="foot-head" style="left:297px">Other Links</div>
  <ul class="foot-links" style="left:297px">
    <li>➔ FAQ</li><li>➔ Terms of Use</li><li>➔ Privacy Policy</li><li>➔ Support Links</li><li>➔ Conditions</li>
  </ul>
  <div class="foot-head" style="left:507px">Contact Us</div>
  <div class="contact" style="top:111px"><i><svg width="14" height="16" viewBox="0 0 14 16" fill="#111"><path d="M7 0a6 6 0 0 0-6 6c0 4.5 6 10 6 10s6-5.5 6-10a6 6 0 0 0-6-6zm0 8.5A2.5 2.5 0 1 1 7 3.5a2.5 2.5 0 0 1 0 5z"/></svg></i>Company Name,United State.</div>
  <div class="contact" style="top:171px"><i><svg width="16" height="12" viewBox="0 0 16 12" fill="#111"><path d="M0 0h16v12H0z"/><path d="M0 0l8 6 8-6" stroke="#f7c9bd" stroke-width="1.4" fill="none"/></svg></i>hello@snoutsaver.net</div>
  <div class="contact" style="top:232px"><i><svg width="15" height="15" viewBox="0 0 15 15" fill="#111"><path d="M3 0l3 4-2 2c1 2 3 4 5 5l2-2 4 3-2 3C6 15 0 9 0 3z"/></svg></i>+1888 8888 8888</div>
  <div class="foot-head" style="left:828px">Sign Up To Our Newsletter</div>
  <p class="news-copy">Lorem ipsum dolor sit amet,consectetur adipiscing elit,adipiscing elit.</p>
  <div class="news-input">Email</div>
  <div class="btn subscribe">Subscribe</div>
  <div class="foot-rule"></div>
  <div class="copyright">Copyrights@2025.Company Name.All Rights Reserved</div>
</footer>

</body>
</html>
```